Need a new company business card

I am looking for a new company business card. Front and back. With information on it as per below. Card should be professional. Yet clever. Simple. Modern design. Pim card, traditional size. OK with say, all black or all red backside.

Varnholt is an indie, bootstrapped magazine advancing the work of intersectional feminists busting their buts to create a just world through the power of enterprise and innovation.

Varnholt is the home and voice of entrepreneurial feminism and feminist innovators worldwide. Entrepreneurial feminists are people (of all genders) who see inequality as an innovation priority. They work to advance gender equity and/or who strive to integrate and practice feminist principles, pedagogy, values into their innovation and entrepreneurship work.
We are committed to this space being trans and queer inclusive, anti-racist, intersectional, brave, and safe. We welcome all allies. We value learning, edgy but civil discourse and integrative thinking skills.

Target Market(s)

feminists, business owners,

Industry/Entity Type

Publishing Company

Contact Information for Business Card

RD Tolliver
Founder/Publisher
4-237 Ashgrove Lane, Toronto, ON
M4T 2K8
publisher@varnholt.com
416-552-3019
www.varnholt.com

Font styles to use
Serif
Other font styles liked:
• Myriad Pro

Colors
ec1f27
000000
ffffff

Requirements
Must have
• logo
• use red, black white colours only.
Nice to have
• use the compass in pattern or creatively but not too busy please
Should not have
• Should not be too busy. Elegant.

```html
<!DOCTYPE html>
<html lang="en">
<head>
<meta charset="utf-8">
<title>Varnholt business card</title>
<link href="https://fonts.googleapis.com/css2?family=Roboto:wght@400&family=Roboto+Condensed:wght@700&display=swap" rel="stylesheet">
<style>
  :root {
    --red: #ec1f27;
    --ink: #333333;
    --black: #000000;
    --white: #ffffff;
    --paper: #f4f4f4;
    --band: #333333;
    --rule: #c8c8c8;
    --stage: #e6e6e6;
  }
  html, body {
    margin: 0;
    padding: 0;
    width: 1200px;
    height: 960px;
    overflow: hidden;
    background: var(--stage);
  }
  .canvas {
    position: relative;
    width: 1200px;
    height: 960px;
  }
  .card {
    position: absolute;
    width: 600px;
    height: 343px;
    box-shadow: 0 2px 6px rgba(0,0,0,0.25);
    overflow: hidden;
  }
  .card-front { left: 314px; top: 113px; background: var(--paper); }
  .card-back  { left: 312px; top: 472px; background: var(--red); }

  .back-pattern {
    position: absolute;
    inset: 0;
    background: var(--red);
  }

  .wordmark {
    position: absolute;
    font-family: "Roboto Condensed", sans-serif;
    font-weight: 700;
    line-height: 1;
    margin: 0;
    white-space: nowrap;
  }
  .front-wordmark {
    left: 40px; width: 260px;
    text-align: center;
    top: 141px;
    font-size: 44px;
    color: var(--ink);
  }
  .back-wordmark {
    left: 0; width: 600px;
    text-align: center;
    top: 137px;
    font-size: 68px;
    color: var(--white);
  }

  .badge { position: absolute; }
  .front-badge { left: 279px; top: 122px; }
  .back-badge  { left: 439px; top: 108px; }

  .divider {
    position: absolute;
    left: 316px; top: 82px;
    width: 1px; height: 160px;
    background: var(--rule);
  }
  .contact {
    position: absolute;
    left: 344px; top: 86px;
    font-family: "Roboto", sans-serif;
    color: var(--ink);
  }
  .contact-name {
    font-family: "Roboto Condensed", sans-serif;
    font-weight: 700;
    font-size: 21px;
    margin: 0;
    line-height: 1;
    text-transform: uppercase;
  }
  .contact-title {
    font-family: "Roboto Condensed", sans-serif;
    font-weight: 700;
    font-size: 15px;
    color: var(--red);
    margin: 4px 0 0;
  }
  .contact-address {
    font-size: 14px;
    line-height: 19px;
    margin: 22px 0 0;
    font-style: normal;
  }
  .contact-lines {
    list-style: none;
    padding: 0;
    margin: 10px 0 0;
    font-size: 14px;
    line-height: 20px;
  }
  .contact-lines li { display: flex; align-items: center; gap: 8px; }
  .contact-lines svg { width: 13px; height: 13px; fill: var(--ink); }

  .web-band {
    position: absolute;
    left: 0; top: 295px;
    width: 600px; height: 32px;
    background: var(--band);
    border-top: 2px solid var(--red);
    border-bottom: 2px solid var(--red);
    box-shadow: 0 -4px 0 -2px var(--paper), 0 -5px 0 -2px var(--red);
  }
  .web-address {
    margin: 0;
    text-align: center;
    line-height: 32px;
    font-family: "Roboto", sans-serif;
    font-size: 14px;
    letter-spacing: 4.5px;
    color: var(--white);
  }
</style>
</head>
<body>
<main class="canvas">

  <section class="card card-front" aria-label="Card front">
    <h1 class="wordmark front-wordmark">Varnholt</h1>
    <svg class="badge front-badge" width="12" height="12" viewBox="0 0 12 12" aria-hidden="true">
      <circle cx="6" cy="6" r="5" fill="none" stroke="#333333" stroke-width="1.2"/>
    </svg>

    <div class="divider"></div>

    <div class="contact">
      <p class="contact-name">RD Tolliver</p>
      <p class="contact-title">Founder/Publisher</p>
      <address class="contact-address">4-237 Ashgrove Lane<br>Toronto, ON, M4T 2K8</address>
      <ul class="contact-lines">
        <li>
          <svg viewBox="0 0 24 24" aria-hidden="true"><path d="M6.6 10.8a15.1 15.1 0 0 0 6.6 6.6l2.2-2.2a1 1 0 0 1 1-.25 11.4 11.4 0 0 0 3.6.57 1 1 0 0 1 1 1V20a1 1 0 0 1-1 1A17 17 0 0 1 3 4a1 1 0 0 1 1-1h3.5a1 1 0 0 1 1 1c0 1.25.2 2.45.57 3.57a1 1 0 0 1-.25 1z"/></svg>
          416-552-3019
        </li>
        <li>
          <svg viewBox="0 0 24 24" aria-hidden="true"><path d="M2 5h20v14H2z"/><path d="M3 6l9 7 9-7" fill="none" stroke="#f4f4f4" stroke-width="1.6"/></svg>
          publisher@varnholt.com
        </li>
      </ul>
    </div>

    <div class="web-band">
      <p class="web-address">www.varnholt.com</p>
    </div>
  </section>

  <section class="card card-back" aria-label="Card back">
    <div class="back-pattern" role="img" aria-label="Fine repeating red-on-red pattern background"></div>
    <p class="wordmark back-wordmark">Varnholt</p>
    <svg class="badge back-badge" width="18" height="18" viewBox="0 0 18 18" aria-hidden="true">
      <circle cx="9" cy="9" r="8" fill="none" stroke="#ffffff" stroke-width="1.6"/>
    </svg>
  </section>

</main>
</body>
</html>
```